Homemaking training schools needs a Business Card design

Designer, Hello!

No special requirements, good-looking enough.
--------------------------------------------------------------------------

Name: Marcus Dole
Chairman
Tel: 0574-71948263
Mobile: 13857420916
Email: kelvora@mailnest.example
Web: www.prt2019.example
Add: No.258, LanpingJie, BeiyuanQu, Ningbo, Zhejiang

LOGO
Ningbo PRT Homemaking Training School

Target Market(s)

pregnant women, mothers, infants, the elderly and families, including cleaning, cooking, nursing training.

Industry/Entity Type

Business

Contact Information for Business Card

Name: Marcus Dole
Chairman
Tel: 0574-71948263
Mobile: 13857420916
Email: kelvora@mailnest.example
Web: www.prt2019.example

LOGO

Font styles to use
Serif
Sans Serif
Decorative

Requirements
Nice to have
• Feels: clean, specifications, safety, comfort, warmth and happiness.

```html
<!DOCTYPE html>
<html lang="en">
<head>
<meta charset="utf-8">
<title>PinRuiTang Business Card</title>
<link rel="stylesheet" href="https://fonts.googleapis.com/css2?family=Open+Sans:wght@400;600;700&display=swap">
<style>
  :root {
    --brand-blue: #1f6fb8;
    --brand-pink: #e4168b;
    --text-grey: #555555;
    --rule-grey: #b9b9b9;
    --card-white: #ffffff;
    --page-bg: #e9e9e9;
  }
  * { margin: 0; padding: 0; box-sizing: border-box; }
  html, body {
    width: 1105px;
    height: 1200px;
    overflow: hidden;
    background: var(--page-bg);
    font-family: "Open Sans", Arial, sans-serif;
  }
  .card {
    position: absolute;
    left: 196px;
    width: 720px;
    height: 412px;
    background: var(--card-white);
  }
  .card--front { top: 146px; }
  .card--back { top: 602px; }

  .brand {
    position: absolute;
    top: 196px;
    left: 0;
    width: 100%;
    display: flex;
    justify-content: center;
    align-items: center;
    gap: 12px;
  }
  .brand__dot {
    width: 18px;
    height: 18px;
    border-radius: 50%;
    background: var(--brand-pink);
  }
  .brand__name {
    font-size: 42px;
    font-weight: 600;
    line-height: 1;
    color: var(--brand-blue);
  }

  .holder {
    position: absolute;
    top: 99px;
    left: 0;
    width: 100%;
    text-align: center;
  }
  .holder__name {
    font-size: 25px;
    font-weight: 600;
    color: var(--brand-blue);
    letter-spacing: 0.5px;
    line-height: 36px;
  }
  .holder__rule {
    position: relative;
    margin: 0 auto;
    width: 448px;
    height: 26px;
  }
  .holder__rule::before {
    content: "";
    position: absolute;
    left: 0;
    right: 0;
    top: 13px;
    border-top: 1.5px solid var(--rule-grey);
  }
  .holder__title {
    position: relative;
    display: inline-block;
    padding: 0 4px;
    background: var(--card-white);
    font-size: 19px;
    font-weight: 600;
    color: var(--brand-pink);
    letter-spacing: 1px;
    line-height: 26px;
  }

  .contact {
    position: absolute;
    top: 222px;
    left: 0;
    width: 100%;
    text-align: center;
    font-size: 19px;
    color: var(--text-grey);
    line-height: 27.5px;
  }
  .contact__label {
    font-weight: 700;
    color: var(--brand-pink);
  }
</style>
</head>
<body>
  <section class="card card--front">
    <div class="brand">
      <span class="brand__dot"></span>
      <span class="brand__name">PinRuiTang</span>
    </div>
  </section>

  <section class="card card--back">
    <div class="holder">
      <h1 class="holder__name">MARCUS DOLE</h1>
      <div class="holder__rule"><span class="holder__title">CHAIRMAN</span></div>
    </div>
    <div class="contact">
      <p class="contact__line">No.258, LanpingJie, BeiyuanQu, Ningbo, Zhejiang</p>
      <p class="contact__line"><span class="contact__label">P :</span> 0574-71948263 <span class="contact__label">M :</span> 13857420916</p>
      <p class="contact__line"><span class="contact__label">E :</span> kelvora@mailnest.example&nbsp; <span class="contact__label">W :</span> www.prt2019.example</p>
    </div>
  </section>
</body>
</html>
```